Banner Ad Design Project

I need a banner design for a new application which is going to the displayed on the PlugBazaar.

The banner is needed for this application:
https://pages.tovrel-cloud.example/plugbazaar/itemView?itemId=k7Q52000001mzpwRTB

Example banners can be found here:
https://pages.tovrel-cloud.example/plugbazaar/itemView?itemId=k7Q52000008hdrsRTB

Or
https://pages.tovrel-cloud.example/plugbazaar/itemView?itemId=k7Q52000005nWKPRT4

Target Market(s)

Enterprise business.

Requirements
Must have
• Must include our brindlecore logo.

```html
<!DOCTYPE html>
<html lang="en">
<head>
<meta charset="utf-8">
<title>Approval History Reporting – Brindlecore</title>
<link rel="stylesheet" href="https://fonts.googleapis.com/css2?family=Oswald:wght@500&family=Nunito:wght@600;700&display=swap">
<style>
  :root {
    --sky-top: #1f86d6;
    --sky-mid: #4fb0ee;
    --sky-low: #a9dcfa;
    --cloud: #ffffff;
    --ink-white: #ffffff;
    --brand-ink: #3a7fc4;
    --brand-dot: #f2a01d;
    --sub-ink: #eaf6ff;
    --cube-top: #ffffff;
    --cube-left: #cfe6f7;
    --cube-right: #9fc9ea;
    --photo-a: #8fcaf2;
    --photo-b: #d7b39a;
    --photo-c: #c7e6fa;
  }
  * { box-sizing: border-box; margin: 0; padding: 0; }
  html, body { width: 1200px; height: 103px; overflow: hidden; background: #ffffff; }

  .banner {
    position: relative;
    width: 1200px;
    height: 103px;
    overflow: hidden;
    background: linear-gradient(180deg, var(--sky-top) 0%, var(--sky-mid) 55%, var(--sky-low) 100%);
  }

  .cloud-panel {
    position: absolute;
    left: 0; top: 0;
    width: 300px; height: 103px;
  }

  .brand {
    position: absolute;
    left: 22px; top: 32px;
    display: flex;
    align-items: center;
    gap: 10px;
  }
  .brand-dot {
    width: 34px; height: 34px;
    border-radius: 50%;
    background: var(--brand-dot);
  }
  .brand-name {
    font-family: "Nunito", sans-serif;
    font-weight: 600;
    font-size: 24px;
    color: var(--brand-ink);
  }

  .headline {
    position: absolute;
    left: 300px; width: 540px;
    top: 4px;
    text-align: center;
    font-family: "Oswald", sans-serif;
    font-weight: 500;
    font-size: 42px;
    line-height: 54px;
    color: var(--ink-white);
    letter-spacing: 0.5px;
    text-shadow: 0 1px 2px rgba(0, 40, 90, 0.35);
  }

  .tagline {
    position: absolute;
    left: 300px; width: 540px;
    top: 64px;
    display: flex;
    justify-content: center;
    align-items: center;
    gap: 10px;
    font-family: "Nunito", sans-serif;
    font-weight: 700;
    font-size: 22px;
    line-height: 28px;
    color: var(--sub-ink);
    letter-spacing: 0.8px;
  }
  .cube { width: 18px; height: 18px; display: block; }

  .photo-area {
    position: absolute;
    left: 830px; top: 0;
    width: 370px; height: 103px;
    background: linear-gradient(90deg, rgba(143,202,242,0) 0%, var(--photo-a) 12%, var(--photo-b) 45%, var(--photo-c) 75%, var(--photo-b) 100%);
  }
</style>
</head>
<body>
  <div class="banner">
    <svg class="cloud-panel" viewBox="0 0 300 103" aria-hidden="true">
      <path fill="var(--cloud)" d="M0 0 H262 C248 10 250 22 262 28 C280 34 282 52 266 58 C282 66 278 86 258 88 C250 96 238 103 226 103 H0 Z"/>
    </svg>

    <div class="brand">
      <span class="brand-dot"></span>
      <span class="brand-name">Brindlecore</span>
    </div>

    <h1 class="headline">Approval History Reporting</h1>

    <p class="tagline">
      <span>Monitoring</span>
      <svg class="cube" viewBox="0 0 18 18" aria-hidden="true">
        <polygon points="9,1 17,5 9,9 1,5" fill="var(--cube-top)"/>
        <polygon points="1,5 9,9 9,17 1,13" fill="var(--cube-left)"/>
        <polygon points="17,5 9,9 9,17 17,13" fill="var(--cube-right)"/>
      </svg>
      <span>Tracking</span>
      <svg class="cube" viewBox="0 0 18 18" aria-hidden="true">
        <polygon points="9,1 17,5 9,9 1,5" fill="var(--cube-top)"/>
        <polygon points="1,5 9,9 9,17 1,13" fill="var(--cube-left)"/>
        <polygon points="17,5 9,9 9,17 17,13" fill="var(--cube-right)"/>
      </svg>
      <span>Approving</span>
    </p>

    <div class="photo-area" role="img" aria-label="Photo of many raised hands giving a thumbs up against a blue sky"></div>
  </div>
</body>
</html>
```